SitePress Direct-Booking Website for Bend, Oregon Vacation Rental — $750 Budget
Project Overview

We are looking for a talented SitePress designer/developer to create a clean, professional and inviting direct-booking website for Birch Lantern Retreat, an established short-term vacation rental in Bend, Oregon.

The property is currently successfully listed on Staynest and Hoplo. Our Staynest property has approximately a 4.98-star rating with more than 200 reviews, is an Staynest Visitor Pick, and ranks among the Top 1% of eligible homes.

Project Budget: $750

We will select the designer based on the quality of the initial concept, understanding of the property, proposed booking solution and ability to deliver a completed and functioning SitePress website.

Existing Staynest Listing

Please use our current Staynest listing as the primary reference for photographs, property details, amenities and design inspiration:

https://www.staynest-example.net/rooms/48172036

Original high-resolution photographs and additional property information will be provided to the selected designer.

Design Direction

We want the website to feel:

Upscale but comfortable
Warm and welcoming
Clean and uncluttered
Pacific Northwest / Central Oregon
Professional rather than corporate
Highly visual with large property photographs
Easy to navigate
Excellent on phones, tablets and desktop computers

We welcome creativity and want designers to show us their vision for the property rather than simply copying our Staynest listing.

The website should immediately communicate that Birch Lantern Retreat is a highly rated vacation rental in an excellent Bend location.

Key Property Features
3 bedrooms
2 bathrooms
Sleeps up to 6 guests
Pet friendly
Approximately a 5-minute walk to Bend's Tannery Row Quarter
Near restaurants, shopping and Larkspur Fields Pavilion
Private fenced backyard
Covered outdoor area
Off-street driveway parking
Fireplace
Well-equipped kitchen
Staynest Prime Keeper
Staynest Visitor Pick
Top 1% of eligible Staynest homes
Approximately 4.98 stars with 200+ guest reviews

Our location, guest reviews, cleanliness, comfort, backyard, pet-friendly accommodations and walkability should be major selling points throughout the website.

Website Structure

We anticipate approximately 6–7 pages:

Home

Large hero photograph with a strong opening message and prominent BOOK DIRECT and CHECK AVAILABILITY buttons.

The home page should quickly communicate:

BIRCH LANTERN RETREAT — BEND, OREGON

3 Bedrooms | 2 Baths | Sleeps 6 | Pet Friendly | Walk to Tannery Row

Our exceptional guest rating and Staynest history should also be prominently featured.

The House

Bedrooms, bathrooms, kitchen, living areas, backyard and major amenities.

Photo Gallery

Large, attractive and fast-loading photographs with an easy-to-use mobile gallery.

Location / Explore Bend

Tannery Row Quarter, Larkspur Fields Pavilion, Deschutes River, restaurants, breweries, shopping, downtown Bend and nearby outdoor recreation.

Guest Reviews

Selected guest reviews and prominent presentation of our strong Staynest reputation.

Availability & Book Direct

A simple and professional direct-booking experience.

Contact / FAQ

Contact information plus common questions regarding pets, parking, check-in/check-out, cancellations and other policies.

IMPORTANT — Direct Booking & Credit Card Requirements

We want guests to be able to book directly through the website without having to contact us first.

The website should use a proven SitePress vacation-rental booking plugin or system rather than a custom-built reservation/payment system.

Guests should be able to:

Select arrival and departure dates
See available dates
Enter number of guests
See nightly charges
See cleaning fees
See applicable lodging taxes and other charges
See the complete reservation total before paying
Enter guest/contact information
Pay securely by credit or debit card
Receive an automatic reservation confirmation

Paywell is our preferred credit-card processor.

Credit-card information must be processed securely through Paywell or another established payment processor. Credit-card information should NOT be stored directly on our SitePress website.

Staynest & Hoplo Calendar Synchronization

This is very important.

The direct-booking calendar must synchronize with our existing Staynest and Hoplo calendars to reduce the possibility of double bookings.

For this single-property website, we prefer a simple solution using Staynest/Hoplo calendar or iCal synchronization rather than an expensive monthly channel-management service, if practical.

The designer should clearly identify the booking plugin/system they propose using.

IMPORTANT — Tell Us Your Proposed Booking Solution

As part of your submission, please tell us:

Which SitePress booking plugin/system you recommend.
Whether it synchronizes availability with Staynest and Hoplo.
Whether it integrates directly with Paywell.
The initial cost of the plugin/software.
Any annual or monthly fees.
Whether any additional paid software or services will be required.

We strongly prefer a solution with little or no ongoing monthly software expense.

We do not want to select a designer and later discover that the proposed booking system requires an expensive monthly subscription.

SitePress & Technical Requirements

The completed project should include:

Fully functioning SitePress website
Responsive desktop/tablet/mobile design
Fast-loading pages
Optimized photographs
SSL/HTTPS compatibility
Direct-booking functionality
Paywell payment integration
Staynest calendar synchronization
Hoplo calendar synchronization
Automatic booking confirmations
Cleaning fee and lodging-tax calculations
Contact form
Vizor Maps/location integration
Basic spam/security protection
Vizor Metrics capability
Basic SEO setup
Search-engine submission capability
Easy owner editing of text, rates and photographs
Search Engine Optimization

The website should be structured for Vizor and other search engines.

Important search themes include:

Bend Oregon vacation rental
Bend Oregon vacation home
Tannery Row Quarter vacation rental
Vacation rental near Tannery Row Bend
Bend Oregon pet-friendly vacation rental
Bend vacation rental near Larkspur Fields Pavilion
Bend Oregon direct booking vacation rental

We are not expecting an extensive ongoing SEO campaign for the $750 project. We do expect proper page titles, descriptions, headings, image optimization and a good technical foundation for future SEO.

Ownership

Upon completion and final payment:

We own the completed SitePress website.
We receive full SitePress administrator access.
We control the domain and hosting accounts.
We own all custom design files created for the project.
All necessary login credentials are provided to us.
The website can be moved to another SitePress hosting provider in the future.
There should be no proprietary dependency on the developer after completion.
What We Want From Contestants

Please review our Staynest listing before submitting your concept.

We are particularly interested in seeing an initial homepage concept showing how you would present:

Birch Lantern Retreat
The Bend / Tannery Row location
Our photography
Our exceptional guest reviews and ratings
The Book Direct message
The availability/booking call-to-action

We will provide feedback on the concepts we like and work with the selected designer to refine and complete the website.

Our Goal

Our objective is straightforward:

Create a beautiful, trustworthy and easy-to-use website that encourages guests to book Birch Lantern Retreat directly with us.

The website will complement—not replace—our existing Staynest and Hoplo listings.

We want repeat guests and new customers to have an easy way to find the property, check availability and book directly while receiving the same professional experience they expect from a major vacation-rental platform.

Target Market(s)

Consumers looking to to travel to Mexico for vacation. Family or couples

Industry/Entity Type

Short term vacation rental industry

Coding

Coded - Design and coding required

Number of Pages Required

5+ page

Requirements
Must have
• Capabilities to accept credit card payments and link to other rental property sites calendars such as HOPLO and Staynset
Nice to have
• Option for best plugins for property rental

```html
<!DOCTYPE html>
<html lang="en">
<head>
<meta charset="utf-8">
<title>Birch Lantern Retreat — Bend, Oregon Vacation Home</title>
<link href="https://fonts.googleapis.com/css2?family=Cormorant+Garamond:wght@500;600;700&family=DM+Sans:wght@400;500;700&display=swap" rel="stylesheet">
<style>
:root{
  --forest:#1c2b23;
  --rust:#a3381f;
  --cream:#f9f4f1;
  --blush:#f1e0d9;
  --ink:#26231f;
  --muted:#6a625d;
  --line:#cbbfb8;
  --gold:#e8a23a;
}
*{box-sizing:border-box;margin:0;padding:0}
html,body{width:1200px;height:4329px;overflow:hidden}
body{font-family:"DM Sans",sans-serif;color:var(--ink);background:var(--cream);position:relative}
.serif{font-family:"Cormorant Garamond",serif}
.abs{position:absolute}
.btn{position:absolute;display:flex;align-items:center;justify-content:center;font-family:"Cormorant Garamond",serif;font-weight:700;font-size:13px;letter-spacing:.06em;text-transform:uppercase;border-radius:4px}
.btn-rust{background:var(--rust);color:#fff}
.btn-ghost{border:1.5px solid #fff;color:#fff}
.section-title{position:absolute;left:0;width:1200px;text-align:center;font-family:"Cormorant Garamond",serif;font-weight:600;font-size:34px;letter-spacing:.02em;text-transform:uppercase}
.section-sub{position:absolute;left:0;width:1200px;text-align:center;font-size:24px;font-weight:500}
.section-lead{position:absolute;left:300px;width:600px;text-align:center;font-size:15px;line-height:29px;color:var(--muted)}

/* header */
.site-header{position:absolute;top:0;left:0;width:1200px;height:89px;background:var(--forest);border-top:4px solid var(--rust)}
.brand{position:absolute;left:111px;top:24px;color:#fff;white-space:nowrap}
.brand-name{font-family:"Cormorant Garamond",serif;font-weight:600;font-size:19px;letter-spacing:.01em}
.brand-place{font-family:"Cormorant Garamond",serif;font-size:12px;letter-spacing:.4em;margin-top:2px;padding-left:27px}
.nav{position:absolute;left:417px;top:38px;display:flex;gap:25px;font-family:"Cormorant Garamond",serif;font-size:12.5px;font-weight:600;color:#e8e2dc;letter-spacing:.02em}
.nav .active{color:#fff;font-weight:700}

/* hero */
.hero{position:absolute;top:89px;left:0;width:1200px;height:558px;background:linear-gradient(100deg,#2c3a2a 0%,#4b5f3c 35%,#6f8260 60%,#8fa0a6 100%)}
.hero-shade{position:absolute;inset:0;background:linear-gradient(90deg,rgba(20,28,22,.55),rgba(20,28,22,.1) 70%)}
.hero-title{position:absolute;left:111px;top:85px;color:#fff;font-family:"Cormorant Garamond",serif;font-size:38px;line-height:50px;text-transform:uppercase;font-weight:500}
.hero-title b{font-weight:700}
.hero-text{position:absolute;left:111px;top:214px;color:#fff;font-size:16px;line-height:29px;width:440px}
.hero-facts{position:absolute;left:111px;top:284px;color:#fff;font-size:16px;font-weight:700;word-spacing:2px}
.rating-box{position:absolute;left:111px;top:333px;width:489px;height:73px;background:rgba(90,100,95,.45);border-radius:4px;color:#fff}
.rating-score{position:absolute;left:27px;top:12px;font-size:29px;color:var(--gold)}
.rating-score small{font-size:11px;color:#fff;margin-left:4px}
.rating-stars{position:absolute;left:27px;top:48px}
.rating-div{position:absolute;left:202px;top:12px;width:1px;height:50px;background:#fff}
.rating-note{position:absolute;left:229px;top:18px;font-size:13px;line-height:19px}

/* intro */
.intro{position:absolute;top:647px;left:0;width:1200px;height:516px;background:var(--cream)}
.stat-card{position:absolute;top:281px;width:232px;height:147px;border:1.5px solid var(--line);border-radius:4px;text-align:center;padding-top:26px}
.stat-card svg{display:block;margin:0 auto}
.stat-value{font-size:18px;margin-top:10px}
.stat-label{font-size:14px;letter-spacing:.2em;color:var(--muted);margin-top:4px}

/* house */
.house{position:absolute;top:1163px;left:0;width:1200px;height:553px;background:var(--blush)}
.photo{position:absolute;border-radius:3px}
.split-title{font-family:"Cormorant Garamond",serif;font-weight:600;font-size:34px;line-height:40px;text-transform:uppercase}
.split-sub{font-size:23px;line-height:29px;font-weight:500}
.split-text{font-size:14px;line-height:23px;color:var(--muted)}

/* features */
.features{position:absolute;top:1800px;left:111px;width:978px;height:135px;display:flex}
.feature{flex:1;text-align:center;border-right:1.5px solid var(--line)}
.feature:last-child{border-right:none}
.feature svg{display:block;margin:0 auto 12px}
.feature-title{font-family:"Cormorant Garamond",serif;font-weight:600;font-size:20px}
.feature-sub{font-size:12.5px;letter-spacing:.15em;color:var(--muted);line-height:16px;margin-top:5px}

/* reviews */
.reviews{position:absolute;top:2411px;left:0;width:1200px;height:613px;background:var(--blush)}
.review-card{position:absolute;top:284px;width:307px;height:204px;background:var(--cream);border:1.5px solid var(--line);border-radius:4px;padding:20px}
.review-text{font-size:12.5px;line-height:20.5px;color:var(--muted);margin-top:14px}
.review-name{font-size:15px;margin-top:12px}

/* explore */
.explore-card-title{position:absolute;top:3536px;font-family:"Cormorant Garamond",serif;font-weight:600;font-size:21px}
.explore-card-text{position:absolute;top:3575px;font-size:14px;line-height:24px;color:var(--muted);width:310px}

/* contact + footer */
.site-footer{position:absolute;top:3876px;left:0;width:1200px;height:453px;background:var(--forest);color:#fff}
.contact-card{position:absolute;top:3780px;left:80px;width:1042px;height:205px;background:var(--rust);border-radius:14px;color:#fff}
.foot-brand{position:absolute;left:111px;top:182px;width:300px}
.foot-brand-name{font-family:"Cormorant Garamond",serif;font-size:22px;font-weight:600;white-space:nowrap}
.foot-head{font-family:"Cormorant Garamond",serif;font-size:16px;letter-spacing:.06em;text-transform:uppercase;margin-bottom:10px}
.foot-links{font-size:14px;line-height:24px}
</style>
</head>
<body>

<header class="site-header">
  <div class="brand">
    <div class="brand-name">BIRCH LANTERN RETREAT</div>
    <div class="brand-place">BEND, OREGON.</div>
  </div>
  <nav class="nav">
    <span class="active">HOME</span><span>THE HOUSE</span><span>GALLERY</span><span>EXPLORE BEND</span><span>REVIEWS</span><span>CONTACT</span>
  </nav>
  <div class="btn btn-rust" style="left:969px;top:25px;width:121px;height:35px">Book Now</div>
</header>

<section class="hero">
  <div role="img" aria-label="Aerial photo of Bend's riverside district with footbridge, trees and colourful flags" style="position:absolute;inset:0"></div>
  <div class="hero-shade"></div>
  <h1 class="hero-title">Stay close to everything.<br><b>Feel right at home.</b></h1>
  <p class="hero-text">A warm, welcoming vacation home just minutes from Bend's Tannery Row Quarter.</p>
  <p class="hero-facts">3 BEDROOMS &nbsp;·&nbsp; 2 BATHS &nbsp;·&nbsp; SLEEPS 6 &nbsp;·&nbsp; PET FRIENDLY</p>
  <div class="rating-box">
    <div class="rating-score">4.98<small>(205 Reviews)</small></div>
    <svg class="rating-stars" width="80" height="14" viewBox="0 0 80 14"><g fill="#e8a23a"><path id="st" d="M7 0l2.1 4.6 5 .5-3.8 3.3 1.1 4.9L7 10.8 2.6 13.3l1.1-4.9L0 5.1l5-.5z"/><use href="#st" x="16"/><use href="#st" x="32"/><use href="#st" x="48"/></g><path d="M71 0l2.1 4.6 5 .5-3.8 3.3 1.1 4.9L71 10.8l-4.4 2.5 1.1-4.9L64 5.1l5-.5z" fill="none" stroke="#e8a23a"/></svg>
    <div class="rating-div"></div>
    <div class="rating-note">One of the most loved homes on<br>Staynest, according to guests</div>
  </div>
  <div class="btn btn-rust" style="left:111px;top:438px;width:122px;height:35px">Book Now</div>
  <div class="btn btn-ghost" style="left:246px;top:438px;width:188px;height:35px">Check Availability</div>
</section>

<section class="intro">
  <h2 class="section-title" style="top:75px">A Bend stay guests keep coming back to</h2>
  <p class="section-sub" style="top:127px">Loved for the location. Remembered for the stay.</p>
  <p class="section-lead" style="top:178px;left:180px;width:840px">With a 4.98-star rating and 200+ reviews, Birch Lantern Retreat has earned a reputation for being clean, comfortable, welcoming, and wonderfully located.</p>

  <div class="stat-card" style="left:111px">
    <svg width="80" height="44" viewBox="0 0 80 44"><path d="M40 2l7 15 16 2-12 11 3 16-14-8-14 8 3-16-12-11 16-2z" fill="var(--rust)"/><path d="M14 12l4 8 9 1-6 6 1 9-8-4-8 4 2-9-7-6 9-1z" fill="var(--forest)"/><path d="M66 12l4 8 9 1-7 6 2 9-8-4-8 4 1-9-6-6 9-1z" fill="var(--forest)"/></svg>
    <div class="stat-value">4.98/5</div><div class="stat-label">Guest Rating</div>
  </div>
  <div class="stat-card" style="left:360px">
    <svg width="60" height="44" viewBox="0 0 60 44"><rect x="3" y="2" width="54" height="18" rx="6" fill="var(--rust)"/><rect x="13" y="9" width="30" height="4" rx="2" fill="#fff"/><g fill="var(--forest)"><path d="M12 24l3 6 6 .5-4.5 4 1.3 6L12 37.5 6.2 40.5l1.3-6L3 30.5l6-.5z"/><path d="M30 24l3 6 6 .5-4.5 4 1.3 6L30 37.5l-5.8 3 1.3-6-4.5-4 6-.5z"/><path d="M48 24l3 6 6 .5-4.5 4 1.3 6L48 37.5l-5.8 3 1.3-6-4.5-4 6-.5z"/></g></svg>
    <div class="stat-value">200+</div><div class="stat-label">Guest Reviews</div>
  </div>
  <div class="stat-card" style="left:609px">
    <svg width="46" height="46" viewBox="0 0 46 46"><path d="M10 2h9l4 12 4-12h9l-7 16h-12z" fill="var(--rust)"/><circle cx="23" cy="30" r="14" fill="var(--rust)"/><circle cx="23" cy="30" r="9" fill="var(--forest)"/><text x="23" y="34" text-anchor="middle" font-size="11" fill="#fff" font-family="DM Sans,sans-serif" font-weight="700">1</text></svg>
    <div class="stat-value">TOP 1%</div><div class="stat-label">Staynest Homes</div>
  </div>
  <div class="stat-card" style="left:858px">
    <svg width="40" height="46" viewBox="0 0 40 46"><path d="M20 2C10 2 3 9 3 18c0 12 17 26 17 26s17-14 17-26C37 9 30 2 20 2z" fill="var(--rust)"/><circle cx="20" cy="18" r="9" fill="#fff"/><rect x="13" y="16" width="14" height="5" rx="2" fill="var(--forest)"/></svg>
    <div class="stat-value">GUEST FAVORITE</div><div class="stat-label">Staynest Recognition</div>
  </div>
</section>

<section class="house">
  <div class="photo" role="img" aria-label="Front exterior of the grey craftsman house with garden" style="left:111px;top:82px;width:238px;height:190px;background:linear-gradient(160deg,#6e9bd0,#5e7a52 60%,#8a8f86)"></div>
  <div class="photo" role="img" aria-label="Bedroom with queen bed and teal dresser" style="left:354px;top:82px;width:316px;height:190px;background:linear-gradient(150deg,#c9c1b4,#8f8474 60%,#4f6c6a)"></div>
  <div class="photo" role="img" aria-label="Dining area with table and chairs" style="left:111px;top:277px;width:182px;height:190px;background:linear-gradient(150deg,#d8d2c7,#8b7d6a 70%,#5a4c3d)"></div>
  <div class="photo" role="img" aria-label="Living room with wood stove and sofas" style="left:297px;top:277px;width:373px;height:190px;background:linear-gradient(150deg,#d6cfc4,#a4968a 55%,#6b5d52)"></div>
  <div class="abs" style="left:748px;top:88px;width:350px">
    <h2 class="split-title">Stay for<br>the house</h2>
    <p class="split-sub" style="margin-top:24px">Come for Bend. Stay for<br>the comfort.</p>
    <p class="split-text" style="margin-top:14px">Birch Lantern Retreat gives you the best of both worlds—a welcoming home to relax in and an unbeatable location for exploring Bend. Gather around the fireplace, cook a meal in the well-equipped kitchen, or step outside into your private fenced backyard.</p>
  </div>
  <div class="btn btn-rust" style="left:750px;top:420px;width:121px;height:35px">Book Now</div>
</section>

<div class="features">
  <div class="feature">
    <svg width="66" height="50" viewBox="0 0 66 50"><rect x="4" y="20" width="52" height="16" rx="3" fill="var(--rust)"/><rect x="12" y="12" width="18" height="10" rx="3" fill="var(--rust)"/><rect x="4" y="36" width="4" height="8" fill="var(--forest)"/><rect x="52" y="36" width="4" height="8" fill="var(--forest)"/><rect x="58" y="6" width="3" height="30" fill="var(--forest)"/><path d="M52 2h14l-3 8h-8z" fill="var(--rust)"/></svg>
    <div class="feature-title">Sleep Well</div><div class="feature-sub">1 King 2 Queen<br>beds</div>
  </div>
  <div class="feature">
    <svg width="54" height="50" viewBox="0 0 54 50"><rect x="3" y="2" width="48" height="14" fill="var(--rust)"/><rect x="26" y="2" width="2" height="14" fill="var(--forest)"/><rect x="3" y="20" width="48" height="28" fill="var(--rust)"/><rect x="7" y="24" width="40" height="3" fill="var(--forest)"/><rect x="26" y="27" width="2" height="21" fill="var(--forest)"/><rect x="9" y="6" width="6" height="2" fill="#fff"/><rect x="38" y="6" width="6" height="2" fill="#fff"/></svg>
    <div class="feature-title">Well-Equipped</div><div class="feature-sub">Full kitchen for<br>easy meals</div>
  </div>
  <div class="feature">
    <svg width="60" height="50" viewBox="0 0 60 50"><rect x="2" y="2" width="56" height="8" fill="var(--forest)"/><rect x="6" y="10" width="48" height="38" fill="var(--rust)"/><rect x="16" y="20" width="28" height="28" fill="var(--forest)"/><path d="M30 26c4 6 7 8 6 14-2 4-10 4-12 0-1-6 4-8 6-14z" fill="var(--rust)"/></svg>
    <div class="feature-title">Cozy Year-Round</div><div class="feature-sub">Gas<br>fireplace</div>
  </div>
  <div class="feature">
    <svg width="56" height="50" viewBox="0 0 56 50"><path d="M28 2l26 20h-6v26H8V22H2z" fill="var(--rust)"/><circle cx="28" cy="34" r="6" fill="#fff"/><circle cx="20" cy="25" r="2.6" fill="#fff"/><circle cx="25" cy="21" r="2.6" fill="#fff"/><circle cx="31" cy="21" r="2.6" fill="#fff"/><circle cx="36" cy="25" r="2.6" fill="#fff"/></svg>
    <div class="feature-title">Bring The Pup</div><div class="feature-sub">Pet<br>friendly</div>
  </div>
  <div class="feature">
    <svg width="54" height="50" viewBox="0 0 54 50"><circle cx="34" cy="16" r="14" fill="#fff" stroke="var(--rust)" stroke-width="3"/><text x="34" y="22" text-anchor="middle" font-size="16" font-weight="700" fill="var(--rust)" font-family="DM Sans,sans-serif">P</text><path d="M34 30v6" stroke="var(--rust)" stroke-width="3"/><path d="M6 30h20l4 8v8H2v-8z" fill="var(--rust)"/><circle cx="9" cy="46" r="3" fill="var(--forest)"/><circle cx="24" cy="46" r="3" fill="var(--forest)"/></svg>
    <div class="feature-title">Park With Ease</div><div class="feature-sub">Dedicated<br>driveway</div>
  </div>
</div>

<div class="abs" style="left:111px;top:2021px;width:240px">
  <h2 class="split-title">Photo<br>gallery</h2>
  <p class="split-sub" style="margin-top:24px">See Yourself Here.</p>
  <p class="split-text" style="margin-top:14px">From cozy mornings inside to relaxed evenings in the backyard, take a closer look at the spaces</p>
</div>
<svg class="abs" style="left:111px;top:2264px" width="46" height="46" viewBox="0 0 46 46" aria-label="View gallery"><circle cx="23" cy="23" r="23" fill="var(--rust)"/><path d="M13 23h18M24 15l8 8-8 8" stroke="#fff" stroke-width="3.5" fill="none" stroke-linecap="round" stroke-linejoin="round"/></svg>
<div class="photo" role="img" aria-label="Living room with TV console" style="left:382px;top:2016px;width:230px;height:310px;background:linear-gradient(180deg,#d6d3cd,#bcb6ab 60%,#8a847b)"></div>
<div class="photo" role="img" aria-label="Bathroom with sage green walls and white vanity" style="left:624px;top:2016px;width:230px;height:310px;background:linear-gradient(180deg,#a6b5a2,#c9ccc4 55%,#e8e6e1)"></div>
<div class="photo" role="img" aria-label="Fenced backyard with chairs and stone patio" style="left:867px;top:2016px;width:230px;height:310px;background:linear-gradient(180deg,#6f8eb3,#7a4a36 35%,#a08670 70%,#c3b29e)"></div>

<section class="reviews">
  <h2 class="section-title" style="top:75px">Guest Reviews</h2>
  <p class="section-sub" style="top:125px">Loved by guests. Proven by hundreds of stays.</p>
  <p class="section-lead" style="top:178px;left:240px;width:720px">With a 4.98-star rating and 200+ guest reviews, Birch Lantern Retreat has earned its reputation through the people who have stayed here.</p>

  <div class="review-card" style="left:111px">
    <svg width="86" height="16" viewBox="0 0 86 16"><g fill="#e8a23a"><path id="rs" d="M8 0l2.4 5.2 5.6.6-4.2 3.8 1.2 5.6L8 12.4 3 15.2l1.2-5.6L0 5.8l5.6-.6z"/><use href="#rs" x="17"/><use href="#rs" x="34"/><use href="#rs" x="51"/></g><path d="M76 1l2.2 4.7 5 .5-3.8 3.4 1.1 5L76 12.1l-4.5 2.5 1.1-5-3.8-3.4 5-.5z" fill="none" stroke="#e8a23a"/></svg>
    <p class="review-text">"Lorem ipsum dolor sit amet, cons ectetur adipiscing elit, sed do eiusmod tempor incididunt ut labore et dolore magna aliqua. quis ipsum suspendisse ultrices."</p>
    <p class="review-name">–&nbsp; John</p>
  </div>
  <div class="review-card" style="left:446px">
    <svg width="86" height="16" viewBox="0 0 86 16"><g fill="#e8a23a"><use href="#rs"/><use href="#rs" x="17"/><use href="#rs" x="34"/><use href="#rs" x="51"/></g><path d="M76 1l2.2 4.7 5 .5-3.8 3.4 1.1 5L76 12.1l-4.5 2.5 1.1-5-3.8-3.4 5-.5z" fill="none" stroke="#e8a23a"/></svg>
    <p class="review-text">"Lorem ipsum dolor sit amet, cons ectetur adipiscing elit, sed do eiusmod tempor incididunt ut labore et dolore magna aliqua. quis ipsum suspendisse ultrices."</p>
    <p class="review-name">–&nbsp; John</p>
  </div>
  <div class="review-card" style="left:781px">
    <svg width="86" height="16" viewBox="0 0 86 16"><g fill="#e8a23a"><use href="#rs"/><use href="#rs" x="17"/><use href="#rs" x="34"/><use href="#rs" x="51"/></g><path d="M76 1l2.2 4.7 5 .5-3.8 3.4 1.1 5L76 12.1l-4.5 2.5 1.1-5-3.8-3.4 5-.5z" fill="none" stroke="#e8a23a"/></svg>
    <p class="review-text">"Lorem ipsum dolor sit amet, cons ectetur adipiscing elit, sed do eiusmod tempor incididunt ut labore et dolore magna aliqua. quis ipsum suspendisse ultrices."</p>
    <p class="review-name">–&nbsp; John</p>
  </div>
  <svg class="abs" style="left:572px;top:521px" width="60" height="6" viewBox="0 0 60 6"><rect width="26" height="5" rx="2.5" fill="var(--rust)"/><circle cx="34" cy="2.5" r="2.5" fill="var(--rust)"/><circle cx="44" cy="2.5" r="2.5" fill="var(--rust)"/><circle cx="54" cy="2.5" r="2.5" fill="var(--rust)"/></svg>
</section>

<section aria-label="Explore Bend">
  <h2 class="section-title" style="top:3104px">Explore Bend</h2>
  <p class="section-sub" style="top:3155px">The best of Bend, right nearby.</p>
  <p class="section-lead" style="top:3210px;left:230px;width:740px;font-size:14px;line-height:24px">Birch Lantern Retreat puts you close to the places that make Bend special—from riverside walks and local breweries to live music, shopping, downtown adventures, and the great outdoors.</p>

  <div class="photo" role="img" aria-label="Craftsman house in the Tannery Row Quarter" style="left:111px;top:3306px;width:310px;height:204px;background:linear-gradient(160deg,#5f86bd,#46603f 55%,#9a9c95)"></div>
  <div class="photo" role="img" aria-label="Deschutes River at sunset with pine trees" style="left:444px;top:3306px;width:311px;height:204px;background:linear-gradient(180deg,#8ea6c4,#c9b08a 35%,#3c4a3c 60%,#2f4150)"></div>
  <div class="photo" role="img" aria-label="Brewery interior with red bar stools" style="left:777px;top:3306px;width:312px;height:204px;background:linear-gradient(180deg,#b9b6b0,#6d6a66 55%,#b4402a 80%,#4a3f38)"></div>

  <h3 class="explore-card-title" style="left:111px">Tannery Row Quarter</h3>
  <p class="explore-card-text" style="left:111px">Walk to shops, restaurants, entertainment, and the Deschutes River.</p>
  <h3 class="explore-card-title" style="left:444px">Deschutes River</h3>
  <p class="explore-card-text" style="left:444px">Explore scenic paths, water activities, and peaceful riverside spots.</p>
  <h3 class="explore-card-title" style="left:777px">Restaurants &amp; Breweries</h3>
  <p class="explore-card-text" style="left:777px">Discover Bend's local food scene and legendary craft beer.</p>

  <div class="btn btn-rust" style="left:524px;top:3660px;width:151px;height:35px">Explore Bend</div>
</section>

<footer class="site-footer">
  <div class="foot-brand">
    <div class="foot-brand-name">BIRCH LANTERN RETREAT</div>
    <div class="serif" style="font-size:13px;letter-spacing:.4em;margin-top:4px">BEND, OREGON.</div>
    <p style="font-size:14px;line-height:23px;margin-top:24px">A warm, welcoming vacation<br>home near Bend's Tannery Row Quarter.</p>
  </div>
  <div class="abs" style="left:441px;top:190px">
    <div class="foot-head">Explore</div>
    <div class="foot-links">The House<br>Gallery<br>Explore Bend<br>Reviews<br>FAQ</div>
  </div>
  <div class="abs" style="left:608px;top:190px">
    <div class="foot-head">Book</div>
    <div class="foot-links">Check Availability<br>Book Direct</div>
    <div class="foot-head" style="margin-top:34px">Follow</div>
    <div class="foot-links">Staynest &nbsp;&nbsp;|&nbsp;&nbsp; Hoplo &nbsp;&nbsp;|&nbsp;&nbsp; Snapframe</div>
  </div>
  <div class="abs" style="left:905px;top:190px">
    <div class="foot-head">Contact</div>
    <div class="foot-links">
      <div><svg width="12" height="14" viewBox="0 0 12 14" style="margin-right:10px"><path d="M6 0a5 5 0 0 0-5 5c0 4 5 9 5 9s5-5 5-9a5 5 0 0 0-5-5z" fill="#fff"/><circle cx="6" cy="5" r="2" fill="var(--forest)"/></svg>Bend, Oregon</div>
      <div><svg width="13" height="10" viewBox="0 0 13 10" style="margin-right:10px"><rect width="13" height="10" rx="1" fill="#fff"/><path d="M0 1l6.5 5L13 1" stroke="var(--forest)" fill="none"/></svg>info@birchlanternretreat.com</div>
    </div>
  </div>
  <div class="abs" style="left:111px;top:376px;width:978px;height:1px;background:#5a655e"></div>
  <div class="abs" style="left:111px;top:400px;font-size:13.5px">© 2026 Birch Lantern Retreat</div>
  <div class="abs" style="left:691px;top:400px;font-size:13.5px">Privacy Policy &nbsp;|&nbsp; Terms &amp; Conditions &nbsp;|&nbsp; Cancellation Policy</div>
</footer>

<section class="contact-card">
  <h2 class="serif abs" style="left:30px;top:30px;font-size:34px;font-weight:500;text-transform:uppercase">Contact &amp; FAQ</h2>
  <p class="abs" style="left:30px;top:82px;font-size:23px;font-weight:500">Good to know before you arrive.</p>
  <p class="abs" style="left:30px;top:124px;width:600px;font-size:15px;line-height:26px">Have a question about your stay? Find quick answers below or get in touch with us directly.</p>
  <div class="btn" style="left:724px;top:113px;width:120px;height:35px;background:#fff;color:var(--rust)">Book Now</div>
  <div class="btn btn-ghost" style="left:860px;top:113px;width:150px;height:35px">Contact Us</div>
</section>

</body>
</html>
```